all natural handmade soap company looking for unique stand out packaging design for bar soaps

we are looking for a unique and stand out on the shelf package design for our hand made soaps for grocery stores. we have a package soap box (picture included) but we are looking for a TOP-NOTCH, CUSTOM, STAND OUT DESIGN FOR THEM. I am supplying our current packaging design, but we want something more unique and STAND OUT. PICTURES i AM INCLUDING ARE: 1: OUR CURRENT PACKAGE DESIGN
2: OUR LIQUID SOAP LABELS (WHICH WE LOVE) AND WOULD LIKE THE BAR SOAPS TO BE SIMILAR
3: WILL BE IN A WHITE BOX WITH A LARGE CUT OUT IN FRONT (SEE SAMPLE BOX BROWN KRAFT).

Target Market(s)

VARIOUS CUSTOMERS. We sell to bright lantern grocers and various grocery stores

Industry/Entity Type

It Company

Requirements
Must have
• cool, unique look that will stand out from a store shelf
• full color acceptable
• our logo on the round part of the package (front)
• please leave a space for bar codes (usually on bottom of box)
• there is a cut out (front) that is there for people to see, feel and smell the soap
• be creative think outside the box open to fresh new designs
Nice to have
• metallic crescent moon (our logo)
Should not have
• organic cannot appear on the front

```html
<!DOCTYPE html>
<html lang="en">
<head>
<meta charset="utf-8">
<title>Solvane Lemon Bar Soap – Front Panel</title>
<link rel="stylesheet" href="https://fonts.googleapis.com/css2?family=Marcellus&family=Rosarivo&display=swap">
<style>
  :root {
    --canvas: #ffffff;
    --ink: #141414;
    --olive: #5b6b2a;
    --sunny: #f5b914;
    --amber: #eeaa1c;
    --tangerine: #f39221;
    --flame: #ef5a1f;
    --cream: #fbf0d6;
    --mist: #f2f2f2;
    --gold-line: #c9a86a;
  }
  * { margin: 0; padding: 0; box-sizing: border-box; }
  html, body {
    width: 1200px;
    height: 1200px;
    overflow: hidden;
    background: var(--canvas);
  }
  .stage {
    position: relative;
    width: 1200px;
    height: 1200px;
  }
  .box-front {
    position: absolute;
    left: 321px;
    top: 126px;
    width: 558px;
    height: 948px;
    display: block;
  }
  .brand-name {
    font-family: "Marcellus", serif;
    font-size: 42px;
    letter-spacing: 4px;
    fill: var(--ink);
  }
  .product-line {
    font-family: "Rosarivo", serif;
    font-size: 32px;
    fill: var(--ink);
  }
  .scent-name {
    font-family: "Marcellus", serif;
    font-size: 40px;
    letter-spacing: 2px;
    fill: var(--olive);
  }
  .tagline {
    font-family: "Rosarivo", serif;
    font-size: 33px;
    fill: var(--ink);
  }
  .net-weight {
    font-family: "Rosarivo", serif;
    font-size: 24px;
    fill: #ffffff;
    letter-spacing: 0.5px;
  }
</style>
</head>
<body>
<main class="stage">
  <svg class="box-front" viewBox="0 0 558 948" xmlns="http://www.w3.org/2000/svg" aria-label="Solvane lemon natural soap box front">
    <defs>
      <linearGradient id="cloud-glow" x1="0" y1="0" x2="0" y2="1">
        <stop offset="0" stop-color="#fbe3a6"/>
        <stop offset="0.45" stop-color="#fcefd2"/>
        <stop offset="1" stop-color="#f4f4f4"/>
      </linearGradient>
      <linearGradient id="soap-tone" x1="0" y1="0" x2="1" y2="1">
        <stop offset="0" stop-color="#f6e3bd"/>
        <stop offset="0.5" stop-color="#f1d39c"/>
        <stop offset="1" stop-color="#e9b86c"/>
      </linearGradient>
      <linearGradient id="swoosh-fire" x1="0" y1="0" x2="1" y2="0">
        <stop offset="0" stop-color="var(--flame)"/>
        <stop offset="0.5" stop-color="var(--tangerine)"/>
        <stop offset="1" stop-color="#fbc64a"/>
      </linearGradient>
      <linearGradient id="lower-yellow" x1="0" y1="0" x2="0" y2="1">
        <stop offset="0" stop-color="var(--amber)"/>
        <stop offset="1" stop-color="var(--sunny)"/>
      </linearGradient>
      <radialGradient id="lemon-tone" cx="0.5" cy="0.45" r="0.6">
        <stop offset="0" stop-color="#ffe27a"/>
        <stop offset="1" stop-color="#e9b420"/>
      </radialGradient>
      <clipPath id="below-window-top">
        <rect x="0" y="300" width="558" height="400"/>
      </clipPath>
    </defs>

    <!-- upper panel -->
    <rect class="top-field" x="0" y="0" width="558" height="300" fill="var(--mist)"/>
    <rect class="cloud-decor" x="0" y="0" width="558" height="110" fill="url(#cloud-glow)" role="img" aria-label="Soft pale yellow cloud decoration"/>

    <!-- brand -->
    <g class="brand-lockup">
      <circle cx="279" cy="96" r="8" fill="var(--olive)"/>
      <text class="brand-name" x="279" y="170" text-anchor="middle">SOLVANE</text>
    </g>
    <text class="product-line" x="292" y="282" text-anchor="middle">Natural Soap</text>

    <!-- soap window -->
    <path class="soap-window" d="M0 300 H558 V545 Q260 650 0 592 Z" fill="url(#soap-tone)" role="img" aria-label="View of the lemon soap bar with orange peel flecks"/>

    <!-- scent badge -->
    <g class="scent-badge" clip-path="url(#below-window-top)">
      <circle cx="280" cy="290" r="181" fill="var(--gold-line)"/>
      <circle cx="280" cy="290" r="179" fill="var(--mist)"/>
    </g>
    <ellipse class="lemon-art" cx="275" cy="345" rx="72" ry="46" fill="url(#lemon-tone)" role="img" aria-label="Illustration of a whole lemon and a lemon half with leaves"/>
    <path id="scent-arc" d="M200 430 Q280 470 360 425" fill="none"/>
    <text class="scent-name"><textPath href="#scent-arc" startOffset="50%" text-anchor="middle">LEMON</textPath></text>

    <!-- lower panel and swoosh -->
    <path class="lower-field" d="M0 600 Q260 700 558 625 V900 H0 Z" fill="url(#lower-yellow)"/>
    <path class="swoosh" d="M0 592 Q260 650 558 545 V640 Q260 705 0 600 Z" fill="url(#swoosh-fire)"/>
    <path class="swoosh-highlight" d="M40 625 Q300 710 558 665" fill="none" stroke="#fff6dc" stroke-width="4" opacity="0.9"/>

    <text class="tagline" x="278" y="795" text-anchor="middle">Handcrafted</text>
    <text class="tagline" x="274" y="838" text-anchor="middle">Artsan Natural Soap</text>

    <!-- net weight band -->
    <rect class="weight-band" x="0" y="900" width="558" height="48" fill="var(--tangerine)"/>
    <text class="net-weight" x="279" y="932" text-anchor="middle">4.5oz ( 127.57 grams )</text>
  </svg>
</main>
</body>
</html>
```